Bright Path Mentors Needs A New Website Design

We need a 8 page website designed for "Bright Path Mentors .ca" similar in design to: "keystone learning hub .com".

The winner/successful candidate on the home page will be asked to complete the following inner pages to complete the project:

About Us
Philosophy
How We Work
Work With Us
Blog
Find A Tutor
Contact

Target Market(s)

Tutoring business clients/children

Industry/Entity Type

Education

Number of Pages Required

5+ page

Font styles to use
Sans Serif

Requirements
Must have
• The attached logo included of course. Similar design to the design provided above in the brief. Clear high quality high resolution images of children in school settings.

```html
<!DOCTYPE html>
<html lang="en">
<head>
<meta charset="utf-8">
<title>About Us – Bright Path Mentors</title>
<link href="https://fonts.googleapis.com/css2?family=Roboto+Slab:wght@300;400;700&family=Roboto:wght@300;400;500&family=Montserrat:wght@400;500;600&display=swap" rel="stylesheet">
<style>
:root{
  --navy:#2c3592;
  --orange:#f7941d;
  --peach:#fdc57a;
  --grey-bg:#ebebeb;
  --text:#555;
  --footer:#161616;
  --white:#fff;
}
*{margin:0;padding:0;box-sizing:border-box}
html,body{width:898px;height:1200px;overflow:hidden}
body{position:relative;font-family:'Roboto',sans-serif;background:var(--white);color:var(--text)}
.abs{position:absolute}
.topbar{left:0;top:0;width:898px;height:35px;background:var(--peach)}
.promo{left:313px;top:9px;font-size:14px;color:#222;font-family:'Roboto',sans-serif}
.social-top{left:660px;top:5px;display:flex;gap:4px}
.ring{width:25px;height:25px;border:1.5px solid #222;border-radius:50%;display:flex;align-items:center;justify-content:center}
.ring svg{width:12px;height:12px;fill:none;stroke:#222;stroke-width:1.6}
.assess{left:812px;top:0;width:86px;height:68px;z-index:3}
.assess span{position:absolute;left:0;top:7px;width:86px;text-align:center;color:var(--white);font-family:'Roboto Slab',serif;font-size:13px;line-height:19px}
.navband{left:0;top:35px;width:898px;height:65px;background:var(--navy);border-bottom:2px solid var(--orange)}
.nav{left:251px;top:62px;display:flex;gap:13px;font-family:'Roboto Slab',serif;font-size:11.5px;color:var(--white);letter-spacing:.1px}
.logo{left:74px;top:5px;width:130px;height:130px;border-radius:50%;background:var(--white);display:flex;align-items:center;justify-content:center;text-align:center;z-index:3}
.logo span{font-family:'Roboto Slab',serif;font-weight:700;color:var(--navy);font-size:14px;line-height:17px}
.hero{left:0;top:100px;width:898px;height:158px;background:linear-gradient(90deg,#8a7360,#c4b39a 35%,#b39a83 65%,#7d8ea6)}
.hero h1{position:absolute;left:73px;top:78px;font-family:'Roboto Slab',serif;font-weight:700;font-size:36px;color:var(--white);text-shadow:0 2px 4px rgba(0,0,0,.3)}
.about-h{left:74px;top:294px;font-family:'Roboto Slab',serif;font-weight:400;font-size:22px;color:var(--navy)}
.about-h em{font-style:normal;color:var(--orange)}
.rule{left:74px;top:326px;width:196px;height:2px;background:var(--navy)}
.about-p{left:74px;top:347px;width:390px;font-size:10px;line-height:18px;font-weight:300;color:#666}
.btn{left:74px;top:438px;width:108px;height:30px;border-radius:15px;background:var(--navy);color:var(--white);font-size:12px;font-weight:500;display:flex;align-items:center;justify-content:center}
.photo{left:499px;top:286px;width:320px;height:195px;background:linear-gradient(135deg,#5d5e58,#c99b84 45%,#d17fb0 70%,#b39a7c);box-shadow:0 8px 10px -4px rgba(0,0,0,.35)}
.features{left:0;top:524px;width:898px;height:380px;background:var(--grey-bg)}
.acc{left:74px;width:357px;height:44px;border:1.5px solid var(--navy);border-radius:22px}
.acc .ico{position:absolute;left:-1.5px;top:-1.5px;width:44px;height:44px;border-radius:50%;background:var(--navy);display:flex;align-items:center;justify-content:center}
.acc .label{position:absolute;left:50px;top:9px;font-family:'Roboto Slab',serif;font-size:18px;color:var(--navy)}
.acc .sign{position:absolute;right:9px;top:6px;font-size:24px;color:var(--navy);font-weight:500}
.acc-body{left:74px;top:615px;width:752px;font-size:10.3px;line-height:19px;font-weight:300;color:#444}
.footer{left:0;top:904px;width:898px;height:250px;background:var(--footer);color:var(--white)}
.flogo{left:74px;top:990px;width:144px;text-align:center}
.flogo .dot{width:34px;height:34px;border-radius:50%;background:var(--white);margin:0 auto 10px}
.flogo span{font-family:'Roboto Slab',serif;font-weight:700;font-size:18px;line-height:22px}
.fcol h3{font-family:'Montserrat',sans-serif;font-weight:600;font-size:13px;letter-spacing:.3px}
.fcol .u{width:78px;height:1.5px;background:var(--white);margin-top:8px}
.links{list-style:none;margin-top:18px;font-family:'Montserrat',sans-serif;font-size:11px;line-height:23.7px}
.links li::before{content:"› ";}
.citem{display:flex;gap:12px;margin-top:17px}
.citem .c{width:30px;height:30px;border:1.5px solid var(--white);border-radius:50%;flex:none;display:flex;align-items:center;justify-content:center}
.citem b{font-family:'Montserrat',sans-serif;font-weight:600;font-size:10px;display:block;margin-bottom:4px}
.citem p{font-family:'Montserrat',sans-serif;font-size:9.5px;line-height:15.5px}
.field{position:absolute;border:1px solid var(--white);border-radius:3px;font-family:'Montserrat',sans-serif;font-size:8.5px;padding:9px 8px}
.submit{left:608px;top:1094px;width:90px;height:29px;background:var(--orange);border-radius:2px;font-family:'Montserrat',sans-serif;font-size:9px;display:flex;align-items:center;justify-content:center;color:var(--white)}
.bottombar{left:0;top:1154px;width:898px;height:46px;background:var(--orange)}
.copy{left:73px;top:1170px;font-family:'Montserrat',sans-serif;font-size:10.5px;color:var(--white)}
.pay{left:520px;top:1167px;display:flex;gap:4px;align-items:center;font-family:'Montserrat',sans-serif;font-weight:600;font-size:11px;color:var(--white)}
.pay .card{height:16px;padding:0 3px;background:var(--white);color:var(--navy);font-size:6.5px;display:flex;align-items:center;border-radius:2px}
.social-bot{left:708px;top:1163px;display:flex;gap:5px}
.social-bot .ring{border-color:var(--white)}
.social-bot .ring svg{stroke:var(--white)}
</style>
</head>
<body>
<svg width="0" height="0" style="position:absolute">
  <symbol id="i-globe" viewBox="0 0 12 12"><circle cx="6" cy="6" r="5"/><path d="M1 6h10M6 1c2.5 3 2.5 7 0 10M6 1c-2.5 3-2.5 7 0 10"/></symbol>
  <symbol id="i-share" viewBox="0 0 12 12"><circle cx="2.5" cy="6" r="1.5"/><circle cx="9.5" cy="2.5" r="1.5"/><circle cx="9.5" cy="9.5" r="1.5"/><path d="M4 5.2l4-2M4 6.8l4 2"/></symbol>
  <symbol id="i-chat" viewBox="0 0 12 12"><path d="M1.5 2h9v6h-5l-3 2.5V8h-1z"/></symbol>
  <symbol id="i-heart" viewBox="0 0 12 12"><path d="M6 10.5L1.5 6A2.5 2.5 0 016 2.8 2.5 2.5 0 0110.5 6z"/></symbol>
  <symbol id="i-mail" viewBox="0 0 12 12"><rect x="1" y="2.5" width="10" height="7"/><path d="M1 2.5l5 4 5-4"/></symbol>
</svg>

<div class="abs topbar"></div>
<div class="abs promo">"First Session Just $35 - Call 1-855-555-0142 Now"</div>
<div class="abs social-top">
  <div class="ring"><svg><use href="#i-globe"/></svg></div>
  <div class="ring"><svg><use href="#i-share"/></svg></div>
  <div class="ring"><svg><use href="#i-chat"/></svg></div>
  <div class="ring"><svg><use href="#i-heart"/></svg></div>
  <div class="ring"><svg><use href="#i-mail"/></svg></div>
</div>
<div class="abs navband"></div>
<svg class="abs assess" viewBox="0 0 86 68"><polygon points="0,0 86,0 86,50 43,68 0,50" fill="#f7941d"/></svg>
<div class="abs assess"><span>Free<br>Assessment</span></div>
<nav class="abs nav"><span>HOME</span><span>ABOUT US</span><span>PHILOSOPHY</span><span>HOW WE WORK</span><span>WORK WITH US</span><span>BLOG</span><span>FIND A TUTOR</span><span>CONTACT</span></nav>
<div class="abs logo"><span>Bright Path<br>Mentors</span></div>

<section class="abs hero" role="img" aria-label="Photo of children in a classroom raising their hands"><h1>ABOUT US</h1></section>

<h2 class="abs about-h">ABOUT <em>BRIGHTPATHMENTORS</em></h2>
<div class="abs rule"></div>
<p class="abs about-p">Tutors are often the unsung heroes of the educational world, playing an important role in helping students gain the knowledge and skills needed to reach their goals. While anyone can claim the title of tutor, there are certain traits that make exceptional tutors like those at Bright Path Mentors stand out from all the rest.</p>
<div class="abs btn">READ MORE</div>
<div class="abs photo" role="img" aria-label="Photo of two smiling schoolgirls reading together at a desk"></div>

<section class="abs features"></section>
<div class="abs acc" style="top:555px"><div class="ico"><svg width="24" height="18" viewBox="0 0 24 18" fill="none" stroke="#fff" stroke-width="1.6"><path d="M1 6l11-5 11 5-11 5z"/><path d="M5 8v5c3 3 11 3 14 0V8"/><path d="M21 7v6"/></svg></div><span class="label">Formal Teacher Training</span><span class="sign">−</span></div>
<p class="abs acc-body">Many tutors are naturally gifted in a certain subject, but understanding common school subjects such as English, math and science doesn’t mean a person can automatically teach it well. Tutors at the top tier level take what they do seriously, and go the extra mile to obtain credentials in their field of expertise. All of our tutors are Ontario Certified Teachers. All have first-hand experience teaching in classrooms, and they draw upon this experience when tutoring students.</p>
<div class="abs acc" style="top:695px"><div class="ico"><svg width="24" height="18" viewBox="0 0 24 18" fill="none" stroke="#fff" stroke-width="1.6"><path d="M1 6l11-5 11 5-11 5z"/><path d="M5 8v5c3 3 11 3 14 0V8"/><path d="M21 7v6"/></svg></div><span class="label">One to one attention</span><span class="sign">+</span></div>
<div class="abs acc" style="top:759px"><div class="ico"><svg width="24" height="18" viewBox="0 0 24 18" fill="none" stroke="#fff" stroke-width="1.6"><path d="M1 6l11-5 11 5-11 5z"/><path d="M5 8v5c3 3 11 3 14 0V8"/><path d="M21 7v6"/></svg></div><span class="label">Confidence building</span><span class="sign">+</span></div>
<div class="abs acc" style="top:823px"><div class="ico"><svg width="24" height="18" viewBox="0 0 24 18" fill="none" stroke="#fff" stroke-width="1.6"><path d="M1 6l11-5 11 5-11 5z"/><path d="M5 8v5c3 3 11 3 14 0V8"/><path d="M21 7v6"/></svg></div><span class="label">Schedule flexibility</span><span class="sign">+</span></div>

<footer class="abs footer"></footer>
<div class="abs flogo" style="color:#fff"><div class="dot"></div><span>Bright Path<br>Mentors</span></div>
<div class="abs fcol" style="left:278px;top:934px;color:#fff"><h3>QUICK LINKS</h3><div class="u"></div>
<ul class="links"><li>Home</li><li>About Us</li><li>Philosophy</li><li>How We Work</li><li>Work With Us</li><li>Contact Us</li></ul></div>
<div class="abs fcol" style="left:424px;top:934px;width:176px;color:#fff"><h3>CONTACT US</h3><div class="u"></div>
<div class="citem"><div class="c"><svg width="10" height="13" viewBox="0 0 10 13"><path d="M5 0a5 5 0 00-5 5c0 4 5 8 5 8s5-4 5-8a5 5 0 00-5-5z" fill="#fff"/><circle cx="5" cy="5" r="1.8" fill="#161616"/></svg></div><div><b>BRIGHTPATHMENTORS,</b><p>1280 Maple Ave #210,<br>Northfield, ON M4X</p></div></div>
<div class="citem"><div class="c"><svg width="8" height="12" viewBox="0 0 8 12"><rect x="0.5" y="0.5" width="7" height="11" rx="1.5" fill="none" stroke="#fff"/><rect x="2" y="2" width="4" height="6" fill="#fff"/></svg></div><div><b>PHONE:</b><p>1-855-555-0142</p></div></div>
<div class="citem"><div class="c"><svg width="12" height="9" viewBox="0 0 12 9"><rect width="12" height="9" rx="1" fill="#fff"/><path d="M0 1l6 4 6-4" fill="none" stroke="#161616"/></svg></div><div><b>Mail:</b><p>info@brightpathmentors.ca</p></div></div></div>
<div class="abs fcol" style="left:608px;top:934px;color:#fff"><h3>WORK WITH US</h3><div class="u"></div></div>
<div class="field" style="left:608px;top:974px;width:104px;height:27px;color:#fff">Name</div>
<div class="field" style="left:719px;top:974px;width:104px;height:27px;color:#fff">Phone</div>
<div class="field" style="left:608px;top:1006px;width:215px;height:27px;color:#fff">Upload Resume<svg style="position:absolute;right:8px;top:7px" width="11" height="11" viewBox="0 0 11 11"><path d="M5.5 0l4 4H7v3H4V4H1.5z M0 8h11v3H0z" fill="#fff"/></svg></div>
<div class="field" style="left:608px;top:1038px;width:215px;height:50px;color:#fff">Message</div>
<div class="abs submit">SUBMIT NOW</div>

<div class="abs bottombar"></div>
<div class="abs copy">Copyright © 2016 Bright Path Mentors. All Right Reserved</div>
<div class="abs pay"><span>PayEase</span><span class="card">CardOne</span><span class="card">NovaPay</span><span class="card">Crestline</span></div>
<div class="abs social-bot">
  <div class="ring"><svg><use href="#i-globe"/></svg></div>
  <div class="ring"><svg><use href="#i-share"/></svg></div>
  <div class="ring"><svg><use href="#i-chat"/></svg></div>
  <div class="ring"><svg><use href="#i-heart"/></svg></div>
</div>
</body>
</html>
```